Help me make landing pages for my web application that are mobile friendly

I need to make 2 mobile friendly landing pages for an application. The 2 pages will be related. First I need a home page and then I need a working page. I do not want to change the color scheme or logos. Just layout and design.

```html
<!DOCTYPE html>
<html lang="en">
<head>
<meta charset="utf-8">
<title>ShiftCover – My Assignment</title>
<link rel="stylesheet" href="https://fonts.googleapis.com/css2?family=Archivo:wght@400;600;700;800&display=swap">
<style>
  :root {
    --page-bg: #ffffff;
    --brand: #5a3e93;
    --brand-soft: #6a4fa3;
    --panel: #161616;
    --avatar-grey: #2d2d2d;
    --avatar-cyan: #25b0d4;
    --white: #ffffff;
    --muted: #6a6a6a;
    --value: #b9b9b9;
    --divider: #333333;
    --pill-blue: #4a7fb5;
    --pill-green: #0a8a2a;
    --track: #2e2e2e;
  }
  * { box-sizing: border-box; margin: 0; padding: 0; }
  html, body {
    width: 778px; height: 1200px; overflow: hidden;
    background: var(--page-bg);
    font-family: "Archivo", Arial, sans-serif;
  }
  .screen {
    position: absolute; left: 172px; top: 180px;
    width: 422px; height: 882px;
    background: var(--brand);
    border-radius: 34px;
    overflow: hidden;
    color: var(--white);
  }
  .status-time {
    position: absolute; left: 38px; top: 20px;
    font-size: 15px; font-weight: 600;
  }
  .status-icons { position: absolute; right: 38px; top: 22px; display: flex; gap: 10px; align-items: center; }
  .brand-name {
    position: absolute; left: 38px; top: 63px;
    font-size: 32px; font-weight: 600; letter-spacing: -0.5px;
    display: flex; align-items: center; gap: 10px;
  }
  .brand-mark { width: 20px; height: 20px; background: var(--white); border-radius: 50%; }
  .header-btn {
    position: absolute; top: 70px; width: 31px; height: 31px;
    background: var(--panel); border-radius: 6px;
    display: flex; align-items: center; justify-content: center;
  }
  .header-btn.profile { left: 318px; }
  .header-btn.menu { left: 354px; }
  .panel {
    position: absolute; left: 0; top: 140px; width: 422px; height: 760px;
    background: var(--panel);
    border-radius: 46px 46px 0 0;
  }
  .tab {
    position: absolute; top: 42px; font-size: 17px; font-weight: 700;
  }
  .tab.current { left: 49px; color: var(--white); }
  .tab.other { left: 215px; color: var(--muted); font-weight: 600; }
  .tab-line { position: absolute; left: 38px; top: 76px; width: 348px; height: 2px; background: var(--divider); }
  .tab-underline { position: absolute; left: 38px; top: 75px; width: 156px; height: 3px; background: var(--white); border-radius: 2px; }
  .card { position: absolute; left: 0; width: 400px; height: 234px; }
  .avatar {
    position: absolute; left: 50px; top: 0; width: 63px; height: 63px;
    border-radius: 10px; display: flex; align-items: center; justify-content: center;
  }
  .avatar.grey { background: var(--avatar-grey); }
  .avatar.cyan { background: var(--avatar-cyan); }
  .avatar.purple { background: var(--brand-soft); }
  .card-title { position: absolute; left: 133px; top: 9px; font-size: 18px; font-weight: 700; }
  .edit-icon { position: absolute; left: 369px; top: 10px; }
  .row-label, .row-value { position: absolute; font-weight: 700; }
  .row-label { left: 133px; font-size: 13px; color: var(--white); }
  .row-value { left: 264px; font-size: 11px; color: var(--value); }
  .pill {
    position: absolute; height: 26px; border-radius: 13px;
    font-size: 11px; font-weight: 700; color: var(--white);
    display: flex; align-items: center; justify-content: center;
  }
  .pill.complete { left: 243px; width: 95px; background: var(--pill-blue); }
  .pill.active { left: 244px; width: 78px; background: var(--pill-green); }
  .card-divider { position: absolute; left: 38px; width: 348px; height: 2px; background: var(--divider); }
  .scroll-track { position: absolute; left: 407px; top: 120px; width: 3px; height: 535px; background: var(--track); border-radius: 2px; }
  .scroll-thumb { position: absolute; left: 407px; top: 120px; width: 3px; height: 125px; background: var(--brand-soft); border-radius: 2px; }
  .bottom-nav {
    position: absolute; left: 15px; top: 813px; width: 393px; height: 69px;
    background: var(--brand); border-radius: 34px;
  }
  .nav-item {
    position: absolute; top: 17px; transform: translateX(-50%);
    display: flex; flex-direction: column; align-items: center; gap: 4px;
    font-size: 12px; font-weight: 700;
  }
</style>
</head>
<body>
<main class="screen">
  <div class="status-time">10:56</div>
  <div class="status-icons">
    <svg width="13" height="11" viewBox="0 0 13 11"><g fill="#fff"><rect x="0" y="8" width="2" height="3"/><rect x="3.5" y="5.5" width="2" height="5.5"/><rect x="7" y="3" width="2" height="8" opacity=".5"/><rect x="10.5" y="0" width="2" height="11" opacity=".5"/></g></svg>
    <svg width="17" height="12" viewBox="0 0 17 12" fill="none" stroke="#fff" stroke-width="1.7" stroke-linecap="round"><path d="M1 4.2a11 11 0 0 1 15 0"/><path d="M3.6 7a7 7 0 0 1 9.8 0"/><circle cx="8.5" cy="10.3" r="1.1" fill="#fff" stroke="none"/></svg>
    <svg width="22" height="11" viewBox="0 0 22 11"><rect x=".6" y=".6" width="18.5" height="9.8" rx="2" fill="none" stroke="#fff" stroke-width="1.2"/><rect x="2.4" y="2.4" width="14.9" height="6.2" fill="#fff"/><rect x="20" y="3.5" width="1.6" height="4" rx=".6" fill="#fff"/></svg>
  </div>

  <div class="brand-name"><span class="brand-mark"></span>ShiftCover</div>

  <div class="header-btn profile">
    <svg width="12" height="12" viewBox="0 0 12 12" fill="#fff"><circle cx="6" cy="3.3" r="2.6"/><path d="M1 12a5 4.5 0 0 1 10 0z"/></svg>
  </div>
  <div class="header-btn menu">
    <svg width="14" height="11" viewBox="0 0 14 11" stroke="#fff" stroke-width="1.4" stroke-linecap="round"><path d="M4 1.5h9M1 5.5h12M6 9.5h7"/></svg>
  </div>

  <section class="panel">
    <div class="tab current">My Assignment</div>
    <div class="tab other">Available Openings</div>
    <div class="tab-line"></div>
    <div class="tab-underline"></div>

    <article class="card" style="top:122px">
      <div class="avatar grey"><svg width="24" height="28" viewBox="0 0 24 28" fill="#fff"><circle cx="12" cy="7" r="6.5"/><path d="M0 28a12 11 0 0 1 24 0z"/></svg></div>
      <div class="card-title">Subbing For:</div>
      <svg class="edit-icon" width="17" height="17" viewBox="0 0 17 17" fill="none" stroke="#cfcfcf" stroke-width="1.4" stroke-linejoin="round"><path d="M8 2.5H2.5v12h12V9"/><path d="M13 1.5l2.5 2.5-7 7H6V8.5z"/></svg>
      <div class="row-label" style="top:43px">Dana Wells</div><div class="row-value" style="top:45px">Teacher</div>
      <div class="row-label" style="top:72px">Location:</div><div class="row-value" style="top:74px">RHES</div>
      <div class="row-label" style="top:103px">Status:</div><div class="pill complete" style="top:97px">Complete</div>
      <div class="row-label" style="top:138px">Time Slots:</div><div class="row-value" style="top:140px">09/02-09/02 (1h 0m)</div>
    </article>
    <div class="card-divider" style="top:316px"></div>

    <article class="card" style="top:355px">
      <div class="avatar cyan"><svg width="24" height="28" viewBox="0 0 24 28" fill="#fff"><circle cx="12" cy="7" r="6.5"/><path d="M0 28a12 11 0 0 1 24 0z"/></svg></div>
      <div class="card-title">Subbing For:</div>
      <svg class="edit-icon" width="17" height="17" viewBox="0 0 17 17" fill="none" stroke="#cfcfcf" stroke-width="1.4" stroke-linejoin="round"><path d="M8 2.5H2.5v12h12V9"/><path d="M13 1.5l2.5 2.5-7 7H6V8.5z"/></svg>
      <div class="row-label" style="top:43px">Tobin Marlow</div><div class="row-value" style="top:45px">Administrator</div>
      <div class="row-label" style="top:72px">Location:</div><div class="row-value" style="top:74px">RHES</div>
      <div class="row-label" style="top:103px">Status:</div><div class="pill active" style="top:97px">Active</div>
      <div class="row-label" style="top:138px">Time Slots:</div><div class="row-value" style="top:140px">07/26 - 08/07 (14h 15m)</div>
    </article>
    <div class="card-divider" style="top:550px"></div>

    <article class="card" style="top:589px">
      <div class="avatar purple"><svg width="24" height="28" viewBox="0 0 24 28" fill="#fff"><circle cx="12" cy="7" r="6.5"/><path d="M0 28a12 11 0 0 1 24 0z"/></svg></div>
      <div class="card-title">Subbing For:</div>
      <svg class="edit-icon" width="17" height="17" viewBox="0 0 17 17" fill="none" stroke="#cfcfcf" stroke-width="1.4" stroke-linejoin="round"><path d="M8 2.5H2.5v12h12V9"/><path d="M13 1.5l2.5 2.5-7 7H6V8.5z"/></svg>
      <div class="row-label" style="top:43px">Extra Duty</div><div class="row-value" style="top:45px">Teacher</div>
      <div class="row-label" style="top:72px">Location:</div><div class="row-value" style="top:74px">RHES</div>
    </article>

    <div class="scroll-track"></div>
    <div class="scroll-thumb"></div>
  </section>

  <nav class="bottom-nav">
    <div class="nav-item" style="left:50px">
      <svg width="20" height="20" viewBox="0 0 20 20"><circle cx="10" cy="10" r="10" fill="#fff"/><path d="M5 10l5-4.5 5 4.5v4.5H5z" fill="#5a3e93"/></svg>Home
    </div>
    <div class="nav-item" style="left:119px">
      <svg width="20" height="20" viewBox="0 0 20 20"><circle cx="10" cy="10" r="10" fill="#fff"/><circle cx="10" cy="7.5" r="3" fill="#5a3e93"/><path d="M4.5 16a5.5 4.5 0 0 1 11 0z" fill="#5a3e93"/></svg>Profile
    </div>
    <div class="nav-item" style="left:195px">
      <svg width="22" height="20" viewBox="0 0 22 20"><path d="M3 10a8 8 0 0 1 16 0" fill="none" stroke="#fff" stroke-width="1.8"/><rect x="1" y="9" width="4" height="6" rx="1.5" fill="#fff"/><rect x="17" y="9" width="4" height="6" rx="1.5" fill="#fff"/><ellipse cx="11" cy="11" rx="5.5" ry="4.5" fill="#fff"/><g fill="#5a3e93"><circle cx="8.7" cy="11" r=".9"/><circle cx="11" cy="11" r=".9"/><circle cx="13.3" cy="11" r=".9"/></g></svg>Support
    </div>
    <div class="nav-item" style="left:273px">
      <svg width="20" height="20" viewBox="0 0 20 20" fill="none" stroke="#fff" stroke-width="2" stroke-linecap="round"><path d="M3.5 6A8 8 0 1 1 2 10"/><path d="M2 3v3.5h3.5"/><path d="M10 6v4.5l3 2"/></svg>History
    </div>
    <div class="nav-item" style="left:343px">
      <svg width="20" height="20" viewBox="0 0 20 20" fill="#fff"><rect x="1" y="1" width="7.5" height="7.5" rx="1.5"/><rect x="11.5" y="1" width="7.5" height="7.5" rx="1.5"/><rect x="1" y="11.5" width="7.5" height="7.5" rx="1.5"/><rect x="11.5" y="11.5" width="7" height="7" rx="1" transform="rotate(45 15 15)"/></svg>More
    </div>
  </nav>
</main>
</body>
</html>
```